BRELWINCare.co.uk - Mental Health Clinic for Child and Adolescents

Updated 29/01/2018***
I am not sure you guys are getting the idea regards to the opening page / homescreen layout. Can you look at the new images I have uploaded (page 5, 6 and 7) These are some of the layouts I like but to incorporate my chosen images, with the BRELWIN commissioner, buttons and a sliding header bar.
I have written a strong brief, I am looking for a website, preferably wordpress as i know they are easy to maintain. I am looking for a one page site, with the top / opening page being full screen image with drop down categories. I have made a rough design, see full brief in word doc attached, there is some freedom to play around with the design aspect but it will need to relay all the content provided. I like a minimal feel. I have also attached some images that may be useful, but will need a new logo for BRELWIN Care. I have attached some logo idea's, it is up to you decide whether you want to use them.
I would prefer the homepage as full screen image, and the categories offered as a drop down or over the main image.
I have also attached linked to some competitors websites:
https://www.vorimant-health.co.uk/
http://www.qlbn.org.uk/
Industry/Entity Type
Clinic
Number of Pages Required
1 page
Font styles to use
Look and feel
Each slider illustrates characteristics of the customer's brand and the style your logo design should communicate.

```html
<!DOCTYPE html>
<html lang="en">
<head>
<meta charset="utf-8">
<title>BRELWIN Care – Every Young Mind Counts</title>
<link href="https://fonts.googleapis.com/css2?family=Montserrat:wght@400;600;700&family=Open+Sans:wght@400;600;700&display=swap" rel="stylesheet">
<style>
:root{
  --purple:#6a1f7a;
  --teal:#3fae9f;
  --blue:#3a8fd8;
  --magenta:#a84fc4;
  --ink:#2b2b2b;
  --muted:#777;
  --rule:#e2e2e2;
  --footer:#262626;
  --footer-deep:#1b1b1b;
  --white:#fff;
}
*{margin:0;padding:0;box-sizing:border-box}
html,body{width:724px;height:1200px;overflow:hidden;background:var(--white)}
body{font-family:"Open Sans",Arial,sans-serif;color:var(--ink);position:relative}

/* hero */
.hero{position:absolute;left:0;top:0;width:724px;height:435px;overflow:hidden}
.hero-photo{position:absolute;inset:0;background:linear-gradient(120deg,#5fb9ad 0%,#3d9f92 45%,#6fbfb2 75%,#4aa699 100%)}
.hero-tint{position:absolute;inset:0;background:rgba(40,150,135,.35)}
.sidebar{position:absolute;left:0;top:0;width:180px;height:330px;background:rgba(35,120,110,.55);z-index:2}
.sidebar-brand{height:86px;background:var(--purple);padding:14px 14px 0;color:var(--white)}
.sidebar-brand .name{font-family:"Montserrat",sans-serif;font-weight:700;font-size:22px;letter-spacing:.5px}
.sidebar-brand .tag{font-size:10px;margin-top:6px}
.nav{list-style:none;padding:18px 0 0 26px}
.nav li{font-family:"Montserrat",sans-serif;font-weight:600;font-size:10px;color:var(--white);letter-spacing:.6px;height:27px}
.hero-content{position:absolute;left:180px;right:0;top:0;bottom:0;text-align:center;color:var(--white);z-index:2}
.hero-logo{margin-top:40px;font-family:"Montserrat",sans-serif;font-weight:700;font-size:56px;letter-spacing:1px}
.hero-tag{font-family:"Montserrat",sans-serif;font-weight:600;font-size:19px;margin-top:2px}
.hero-buttons{margin-top:30px;display:flex;justify-content:center;gap:22px}
.pill{display:inline-block;border:2px solid var(--white);border-radius:22px;padding:9px 30px;font-family:"Montserrat",sans-serif;font-weight:600;font-size:11px;letter-spacing:1px;color:var(--white);text-decoration:none}
.hero-headline{margin-top:66px;font-family:"Open Sans",sans-serif;font-size:27px;line-height:37px;font-weight:400}
.dots{position:absolute;left:180px;right:0;top:402px;display:flex;justify-content:center;gap:5px;z-index:2}
.dots span{width:8px;height:8px;border-radius:50%;border:1px solid var(--white)}
.dots span.on{background:var(--white)}

/* welcome */
.welcome{position:absolute;top:458px;left:0;width:724px;text-align:center}
.section-title{font-family:"Montserrat",sans-serif;font-weight:700;font-size:24px;letter-spacing:.5px;color:var(--ink)}
.welcome p{width:520px;margin:22px auto 0;font-size:10px;line-height:17px;color:#555}
.outline-btn{display:inline-block;margin-top:26px;border:2px solid var(--purple);border-radius:22px;padding:8px 26px;font-family:"Montserrat",sans-serif;font-weight:700;font-size:11px;letter-spacing:1px;color:var(--ink);text-decoration:none}
.divider{position:absolute;top:682px;left:75px;width:574px;height:1px;background:var(--rule)}

/* blog */
.blog{position:absolute;top:718px;left:0;width:724px;text-align:center}
.blog .underline{width:60px;height:2px;background:var(--purple);margin:10px auto 0}
.cards{position:absolute;top:70px;left:90px;display:flex;gap:26px;text-align:left}
.card{width:164px}
.card-photo{height:118px;border:4px solid var(--blue)}
.card.teal .card-photo{border-color:var(--teal)}
.card.violet .card-photo{border-color:var(--magenta)}
.card h3{font-family:"Montserrat",sans-serif;font-weight:600;font-size:10px;margin-top:10px;white-space:nowrap}
.meta{font-size:7.5px;color:var(--muted);margin-top:5px}
.card p{font-size:8px;line-height:12px;color:#555;margin-top:6px}
.read{display:block;margin-top:6px;font-family:"Montserrat",sans-serif;font-weight:700;font-size:8px;color:var(--ink);text-decoration:none}

/* footer */
.footer{position:absolute;top:1040px;left:0;width:724px;height:160px;background:var(--footer);color:#ccc}
.contact{display:flex;justify-content:center;gap:38px;padding-top:26px;font-size:8.5px;align-items:center}
.contact .item{display:flex;align-items:center;gap:7px;line-height:12px}
.ico{width:24px;height:24px;border-radius:50%;border:1px solid #666;display:flex;align-items:center;justify-content:center;flex:none}
.links{display:flex;justify-content:center;gap:9px;margin-top:22px;font-size:9px}
.links span.sep{color:#666}
.bottom{position:absolute;left:0;right:0;bottom:0;height:44px;background:var(--footer-deep);display:flex;align-items:center;justify-content:space-between;padding:0 34px;font-size:8.5px}
.social{display:flex;gap:8px}
.social span{width:20px;height:20px;border-radius:50%;border:1px solid #777;display:block}
</style>
</head>
<body>

<section class="hero">
  <div class="hero-photo" role="img" aria-label="Photo of a group of smiling young people sitting together, under a teal tint"></div>
  <div class="hero-tint"></div>

  <nav class="sidebar">
    <div class="sidebar-brand">
      <div class="name">BRELWIN</div>
      <div class="tag">Every Young Mind Counts</div>
    </div>
    <ul class="nav">
      <li>ABOUT US</li>
      <li>OUR TEAM</li>
      <li>OUR SERVICES</li>
      <li>CONTACT US</li>
      <li>PARENTS</li>
      <li>COMMISSIONERS</li>
      <li>BLOG</li>
      <li>FORUM</li>
    </ul>
  </nav>

  <div class="hero-content">
    <div class="hero-logo">BRELWIN</div>
    <div class="hero-tag">Every Young Mind Counts</div>
    <div class="hero-buttons">
      <a class="pill" href="#">PARENTS</a>
      <a class="pill" href="#">COMMISSIONERS</a>
    </div>
    <h1 class="hero-headline">ADHD and Autism screening<br>within 24 hours</h1>
  </div>
  <div class="dots"><span class="on"></span><span></span><span></span><span></span></div>
</section>

<section class="welcome">
  <h2 class="section-title">WELCOME TO BRELWIN CARE</h2>
  <p>BRELWIN Care was formed with a vision to provide the very best child and adolescent assessment, therapy and aftercare. We have unique clinical pathways that allow children and adolescents to be seen quickly by experienced clinicians who are highly skilled and some of the best in their field. We have a dedicated team of specialists for all ADHD and Autism screening and aim to have any child seen within a few days of referral. If your child has been diagnosed with ADHD or Autism we offer the very best post diagnosis support to both the child and family.</p>
  <a class="outline-btn" href="#">ABOUT US</a>
</section>
<div class="divider"></div>

<section class="blog">
  <h2 class="section-title">LATEST BLOG</h2>
  <div class="underline"></div>
  <div class="cards">
    <article class="card">
      <div class="card-photo" role="img" aria-label="Blog photo of young people chatting indoors" style="background:linear-gradient(135deg,#b9c8d4,#8fa6b8)"></div>
      <h3>Finibus Bonorum et Malorum</h3>
      <div class="meta">▣ 25/08/2017 &nbsp; ● Admin</div>
      <p>Nam libero tempore, cum soluta nobis est eligendi optio cumque nihil impedit quo minus id quod maxime placeat facere.</p>
      <a class="read" href="#">READ MORE</a>
    </article>
    <article class="card teal">
      <div class="card-photo" role="img" aria-label="Blog photo of teenagers sitting together on a bench" style="background:linear-gradient(135deg,#c9d8cf,#9fb9ae)"></div>
      <h3>Finibus Bonorum et Malorum</h3>
      <div class="meta">▣ 25/08/2017 &nbsp; ● Admin</div>
      <p>Nam libero tempore, cum soluta nobis est eligendi optio cumque nihil impedit quo minus id quod maxime placeat facere.</p>
      <a class="read" href="#">READ MORE</a>
    </article>
    <article class="card violet">
      <div class="card-photo" role="img" aria-label="Blog photo of a group of friends outdoors" style="background:linear-gradient(135deg,#d4c6d8,#a993b3)"></div>
      <h3>Finibus Bonorum et Malorum</h3>
      <div class="meta">▣ 25/08/2017 &nbsp; ● Admin</div>
      <p>Nam libero tempore, cum soluta nobis est eligendi optio cumque nihil impedit quo minus id quod maxime placeat facere.</p>
      <a class="read" href="#">READ MORE</a>
    </article>
  </div>
</section>

<footer class="footer">
  <div class="contact">
    <div class="item">
      <span class="ico"><svg width="10" height="12" viewBox="0 0 10 12"><path d="M5 0.5a4 4 0 0 0-4 4c0 3 4 7 4 7s4-4 4-7a4 4 0 0 0-4-4z" fill="none" stroke="#ccc"/><circle cx="5" cy="4.5" r="1.3" fill="#ccc"/></svg></span>
      <span>Ashcombe Suite 4, 12 Larkfield Road,<br>London, N7 3QP</span>
    </div>
    <div class="item">
      <span class="ico"><svg width="11" height="11" viewBox="0 0 11 11"><path d="M2 1l2 2-1 1.5c.7 1.5 1.8 2.6 3.3 3.3L7.8 6.8l2 2-1.3 1.5C5 10 1 6 .7 2.3z" fill="#ccc"/></svg></span>
      <span>0203 555 0148</span>
    </div>
    <div class="item">
      <span class="ico"><svg width="12" height="9" viewBox="0 0 12 9"><rect x=".5" y=".5" width="11" height="8" fill="none" stroke="#ccc"/><path d="M.5 .5l5.5 4.5 5.5-4.5" fill="none" stroke="#ccc"/></svg></span>
      <span>enquiry@brelwincare.co.uk</span>
    </div>
    <div class="item">
      <span class="ico"><svg width="12" height="12" viewBox="0 0 12 12"><circle cx="6" cy="6" r="5" fill="none" stroke="#ccc"/><path d="M6 3v3l2 1.5" fill="none" stroke="#ccc"/></svg></span>
      <span>9am - 5pm Mon-Fri</span>
    </div>
  </div>
  <div class="links">
    <span>About us</span><span class="sep">|</span><span>Our Team</span><span class="sep">|</span><span>Our Services</span><span class="sep">|</span><span>Contact us</span><span class="sep">|</span><span>Parents</span><span class="sep">|</span><span>Commissioners</span><span class="sep">|</span><span>Blog</span><span class="sep">|</span><span>Forum</span>
  </div>
  <div class="bottom">
    <span>Copyrights © 2018, BRELWIN Care. All rights reserved.</span>
    <div class="social"><span></span><span></span><span></span><span></span></div>
  </div>
</footer>

</body>
</html>
```